Brand new letterhead, business card, email signature etc.

We are a financial company in London, UK. Our website is www.marlowvane.com. We're wanting a complete remodel of the company colours, letter head, business cards, email signatures, etc. Looking to keep the same font for the company name. I have upload a colour palette that we want to work with. We're looking for company letterhead for outgoing letters/ correspondence, letterhead for internal documentation, email signatures, e-letters. etc. Ultimately we will redesign the entire website also. It is important that our clients get a strong, secure, warm, trustworthy, solid feeling and first impression.
Updates

Designs look the same

Target Market(s)

Institutional investors, (ultra) high net worth individuals

Industry/Entity Type

Finance, Invesments banking.

Font styles to use
Other font styles liked:
• Current font is "Champagne & Limousines"

Requirements
Must have
• Must use the colours provided on the PDF uploaded to the portal. The purple = main colour. The red = accent colour.
Nice to have
• Nice to use same font as now for the company name "Corvane". Font is "Champagne & Limousines". Nice to have some reference to the old logo flower, but only subtle.
Should not have
• Do not use the colour red from our website. Use the colours provided on the colour palette PDF that I uploaded in the portal.

```html
<!DOCTYPE html>
<html lang="en">
<head>
<meta charset="utf-8">
<title>Corvane stationery</title>
<link href="https://fonts.googleapis.com/css2?family=Jost:wght@300&family=Roboto:wght@300;400;500&family=Arimo&display=swap" rel="stylesheet">
<style>
:root{
  --board:#dfdfdf;
  --paper:#ffffff;
  --plum:#3b2150;
  --plum-deep:#2a1639;
  --plum-light:#553672;
  --ink:#3b2150;
  --text:#444444;
  --muted:#777777;
  --accent:#be1e2d;
}
*{margin:0;padding:0;box-sizing:border-box}
html,body{width:1200px;height:1052px;overflow:hidden;background:var(--board)}
body{position:relative;font-family:'Roboto',sans-serif;color:var(--text)}
.sheet{position:absolute;box-shadow:0 2px 4px rgba(0,0,0,.25)}
.brand{position:absolute;display:flex;align-items:center}
.brand-mark{border:1px solid currentColor;flex:none}
.brand-name{font-family:'Jost',sans-serif;font-weight:300;letter-spacing:.2em;line-height:1;white-space:nowrap}
.band{position:absolute;left:0;bottom:0;width:100%}
.band svg{display:block;width:100%;height:100%}

/* letterhead */
.letterhead{left:49px;top:141px;width:544px;height:769px;background:var(--paper)}
.letterhead .brand{left:27px;top:37px;color:var(--ink)}
.letterhead .brand-mark{width:46px;height:46px}
.letterhead .brand-name{font-size:26px;margin-left:11px}
.letter-contact{position:absolute;left:421px;top:30px;border-left:1px solid var(--accent);padding-left:6px;font-size:7px;line-height:9.4px;color:var(--muted);font-weight:300;font-style:normal;white-space:nowrap}
.letter-contact b{font-weight:500;color:var(--plum)}
.letter-contact p+p{margin-top:5px}
.ico{display:inline-block;width:6px;height:6px;margin-right:3px;vertical-align:-1px}
.greeting{position:absolute;left:49px;top:235px;font-size:12px;font-weight:500;color:var(--plum)}
.letter-body{position:absolute;left:48px;top:272px;width:452px;font-family:'Arimo',sans-serif;font-size:9.2px;line-height:11.2px;color:#555}
.letter-body p+p{margin-top:10px}
.sign-off{position:absolute;left:49px;top:503px;font-size:7px;font-weight:500;color:var(--plum)}
.signature{position:absolute;left:47px;top:541px;width:84px;height:30px;background:linear-gradient(90deg,#ece8f0,#f6f4f8)}
.letterhead .band{height:11px}

/* cards */
.card{width:450px;height:257px}
.card-front{left:626px;top:141px;background:var(--plum);color:#fff}
.card-back{left:626px;top:424px;background:var(--plum);color:#fff}
.signature-block{left:636px;top:686px;width:503px;height:224px;background:var(--paper);color:var(--ink)}

.holder{position:absolute;right:19px;top:27px;text-align:right}
.holder-name{font-size:18px;color:#e8394a;line-height:20px;font-weight:400}
.holder-role{font-size:12px;color:#eee;font-weight:300}
.holder-flag{position:absolute;right:0;top:26px;width:9px;height:34px;background:var(--accent)}

.card-front .brand{left:22px;top:69px}
.card-front .brand-mark{width:58px;height:58px}
.card-front .brand-name{font-size:31px;margin-left:14px}

.details{position:absolute;font-weight:300;white-space:nowrap}
.details b{font-weight:500}
.details .divider{border-top:1px solid;margin:6px 0 5px}
.details .icon-line{display:flex;align-items:center;gap:6px}
.details svg{flex:none}
.card-front .details{left:95px;top:127px;font-size:12.5px;line-height:15px;color:#f2f2f2}
.card-front .divider{border-color:#8e7aa0;width:256px}
.card-front .band{height:10px}

.card-back .pattern{position:absolute;inset:0;background:linear-gradient(100deg,var(--plum-deep) 0%,var(--plum) 55%,var(--plum-light) 100%)}
.card-back .brand{left:132px;top:133px}
.card-back .brand-mark{width:57px;height:57px}
.card-back .brand-name{font-size:33px;margin-left:9px}

.signature-block .brand{left:22px;top:20px}
.signature-block .brand-mark{width:50px;height:50px}
.signature-block .brand-name{font-size:26px;margin-left:12px}
.signature-block .details{left:86px;top:89px;font-size:14px;line-height:16.5px;color:#666}
.signature-block .details b{color:var(--plum)}
.signature-block .divider{border-color:var(--accent);width:276px;opacity:.6}
.signature-block .band{height:13px}
</style>
</head>
<body>

<section class="sheet letterhead">
  <div class="brand"><span class="brand-mark"></span><span class="brand-name">CORVANE</span></div>
  <address class="letter-contact">
    <p><b>Corvane (IOM) Limited</b><br>Harbour Court, Douglas<br>Isle of Man, IM98 2QT</p>
    <p><b>Corvane Group Limited</b><br>9th Floor, 14 Bell Lane<br>London, EC1V 3HN</p>
    <p>
      <svg class="ico" viewBox="0 0 10 10"><path d="M2 1l2 2-1 1.5c.7 1.3 1.4 2 2.5 2.5L7 6l2 2-1.3 1.3C4.5 9 1 5.5.7 2.3z" fill="var(--accent)"/></svg>020-555-0148<br>
      <svg class="ico" viewBox="0 0 10 10"><rect x="1" y="2" width="8" height="6" fill="none" stroke="var(--accent)"/><path d="M1 2l4 3 4-3" fill="none" stroke="var(--accent)"/></svg>info@marlowvane.com<br>
      <svg class="ico" viewBox="0 0 10 10"><circle cx="5" cy="5" r="4" fill="none" stroke="var(--accent)"/><path d="M1 5h8M5 1v8" stroke="var(--accent)"/></svg>www.marlowvane.com
    </p>
  </address>
  <p class="greeting">Dear Mr. Ashford,</p>
  <div class="letter-body">
    <p>Lorem ipsum dolor sit amet, consectetuer adipiscing elit, sed diam nonmmy nibh euismod tincidunt ut laor eet dolore magna aliquam erat volutpat. Ut wisi enim ad minim veniam, quis nostrud exerci tationmcorper suscipit lobortis nisl ut aliquip ex ea commodo consequat. Duis autem vel eum iriure dolor in hendrerit in vulputate velit esse molestie consequat, vel illum dolore eu feugiat</p>
    <p>Rorem ipsum dolor sit amet, consectetuer adipiscing elit, sed diam nonmmy nibh euismod tincidunt ut laor eet dolore magna aliquam erat volutpat. Ut wisi enim ad minim veniam, quis nostrud exerci tationmcorper suscipit lobortis nisl ut aliquip ex ea commodo consequat. Duis autem vel eum iriure dolor in hendrerit in vulputate velit esse molest</p>
    <p>Dorem ipsum dolor sit amet, consectetuer adipiscing elit, sed diam nonmmy nibh euismod tincidunt ut laor eet dolore magna aliquam erat volutpat. Ut wisi enim ad minim veniam, quis nostrud exerci tationmcorper suscipit lobortis nisl ut aliquip ex ea commodo consequat. Duis autem vel eum iriure dolor in hendrerit in suscipit lobortis nisl ut aliquip ex ea commodo consequat. Duis autem vel eum iriure dolor in hendrerit in vulputate velit esse molestie consequat, vel illum</p>
    <p>Sorem ipsum dolor sit amet, consectetuer adipiscing elit, sed diam nonmmy nibh euismod tincidunt ut laor eet dolore magna aliquam erat volutpat. Ut wisi enim ad minim veniam, quis nostrud exerci tationmcorper suscipit lobortis nisl ut aliquip ex ea commodo consequat. Duis autem vel eum iriure dolor in</p>
  </div>
  <p class="sign-off">Sincerely,</p>
  <div class="signature" role="img" aria-label="Handwritten signature"></div>
  <div class="band"><svg viewBox="0 0 544 11" preserveAspectRatio="none"><rect width="544" height="11" fill="var(--plum)"/><polygon points="0,0 398,0 388,11 0,11" fill="var(--accent)"/><polygon points="398,0 407,0 397,11 388,11" fill="#fff"/></svg></div>
</section>

<section class="sheet card card-front">
  <div class="holder"><p class="holder-name">DANIEL ASHFORD</p><p class="holder-role">Manager</p></div>
  <span class="holder-flag"></span>
  <div class="brand"><span class="brand-mark"></span><span class="brand-name">CORVANE</span></div>
  <div class="details">
    <b>Corvane (IOM) Limited</b><br>Harbour Court, Douglas, Isle of Man, IM98 2QT<br>
    <b>Corvane Group Limited</b><br>9th Floor, 14 Bell Lane, London, EC1V 3HN
    <div class="divider"></div>
    <div class="icon-line"><svg width="10" height="10" viewBox="0 0 10 10"><path d="M2 1l2 2-1 1.5c.7 1.3 1.4 2 2.5 2.5L7 6l2 2-1.3 1.3C4.5 9 1 5.5.7 2.3z" fill="#e8394a"/></svg>020-555-0148</div>
    <div class="icon-line"><svg width="10" height="10" viewBox="0 0 10 10"><rect x="1" y="2" width="8" height="6" fill="none" stroke="#e8394a"/><path d="M1 2l4 3 4-3" fill="none" stroke="#e8394a"/></svg>info@marlowvane.com<svg width="10" height="10" viewBox="0 0 10 10" style="margin:0 9px 0 4px"><circle cx="5" cy="5" r="4" fill="none" stroke="#e8394a"/><path d="M1 5h8M5 1v8" stroke="#e8394a"/></svg>www.marlowvane.com</div>
  </div>
  <div class="band"><svg viewBox="0 0 450 10" preserveAspectRatio="none"><rect width="450" height="10" fill="#fff"/><polygon points="0,0 315,0 306,10 0,10" fill="var(--accent)"/><polygon points="315,0 318,0 309,10 306,10" fill="var(--plum)"/></svg></div>
</section>

<section class="sheet card card-back">
  <div class="pattern" role="img" aria-label="Embossed repeating floral tile pattern"></div>
  <div class="brand"><span class="brand-mark"></span><span class="brand-name">CORVANE</span></div>
</section>

<section class="sheet signature-block">
  <div class="brand"><span class="brand-mark"></span><span class="brand-name">CORVANE</span></div>
  <div class="details">
    <b>Corvane (IOM) Limited</b><br>Harbour Court, Douglas, Isle of Man, IM98 2QT<br>
    <b>Corvane Group Limited</b><br>9th Floor, 14 Bell Lane, London, EC1V 3HN
    <div class="divider"></div>
    <div class="icon-line"><svg width="11" height="11" viewBox="0 0 10 10"><path d="M2 1l2 2-1 1.5c.7 1.3 1.4 2 2.5 2.5L7 6l2 2-1.3 1.3C4.5 9 1 5.5.7 2.3z" fill="var(--accent)"/></svg>020-555-0148</div>
    <div class="icon-line"><svg width="11" height="11" viewBox="0 0 10 10"><rect x="1" y="2" width="8" height="6" fill="none" stroke="var(--accent)"/><path d="M1 2l4 3 4-3" fill="none" stroke="var(--accent)"/></svg>info@marlowvane.com<svg width="11" height="11" viewBox="0 0 10 10" style="margin:0 9px 0 4px"><circle cx="5" cy="5" r="4" fill="none" stroke="var(--accent)"/><path d="M1 5h8M5 1v8" stroke="var(--accent)"/></svg>www.marlowvane.com</div>
  </div>
  <div class="band"><svg viewBox="0 0 503 13" preserveAspectRatio="none"><rect width="503" height="13" fill="var(--plum)"/><polygon points="0,0 325,0 314,13 0,13" fill="var(--accent)"/><polygon points="325,0 335,0 324,13 314,13" fill="#fff"/></svg></div>
</section>

</body>
</html>
```